RW Holloway LLC Business Card - Civil Engineering & Consulting Firm

We need a Business Card that is elegant, and masculine.  It is our Professional Civil Engineering & Consulting Company located in San Antonio TX (Not s construction or builder firm- no gears & no tool images please). We provide civil engineering services including  commercial site plans, grading and drainage plans, utility plans, hydraulics and hydrology, land planning, utility coordination, and other general civil engineering services related to commercial and residential development.
We have 2 existing Logos. We would like to convey reliability, strength, trustworthiness and attention to detail.  Blues and orange tones as per logo We are OK with the use of a darker blue in the mix.  We have 2 logo versions - Full Company Name Logo to go on the back of card, & Small Icon Logo for the front w/ personal Info.

Target Market(s)
Architects, Real Estate Developers, Other Strctural Engineers, Surveyers, General Contractors
Industry/Entity Type
Professional Civil Engineering
Contact Information for Business Card
Name, Position, Address, Cell & Office #, email, and company website
Font styles to use
Other font styles liked:
- Avian
Requirements
Should not have
- No Tools, No Gears, no Cranes, or Construction Equipment.

```html
<!DOCTYPE html>
<html lang="en">
<head>
<meta charset="utf-8">
<title>RW Holloway LLC – Business Card</title>
<link rel="stylesheet" href="https://fonts.googleapis.com/css2?family=Montserrat:wght@300;400;500;700&display=swap">
<style>
  :root {
    --page-bg: #e6e6e8;
    --card-white: #ffffff;
    --sky-blue: #78aedb;
    --warm-orange: #e8913a;
    --ink: #1f1f1f;
    --card-shadow: 0 10px 28px rgba(0, 0, 0, 0.22);
  }
  * { box-sizing: border-box; margin: 0; padding: 0; }
  html, body { width: 1200px; height: 900px; overflow: hidden; }
  body {
    background: var(--page-bg);
    font-family: "Montserrat", Arial, sans-serif;
    color: var(--ink);
    position: relative;
  }
  .card {
    position: absolute;
    left: 250px;
    width: 700px;
    height: 400px;
    border-radius: 30px;
    box-shadow: var(--card-shadow);
    overflow: hidden;
  }
  /* Back of card: company name on gradient */
  .card--back {
    top: 36px;
    background: linear-gradient(155deg, var(--sky-blue) 0%, #a9a9aa 45%, var(--warm-orange) 85%);
    display: flex;
    align-items: center;
    justify-content: center;
  }
  .company-name {
    color: var(--card-white);
    font-weight: 300;
    font-size: 44px;
    letter-spacing: 0.16em;
    text-transform: uppercase;
  }
  /* Front of card: personal details */
  .card--front {
    top: 464px;
    background: var(--card-white);
  }
  .accent-tab {
    position: absolute;
    left: 0;
    top: 112px;
    width: 14px;
    height: 48px;
    background: var(--warm-orange);
  }
  .contact-block {
    position: absolute;
    left: 52px;
    top: 104px;
  }
  .person-name {
    color: var(--warm-orange);
    font-weight: 700;
    font-size: 30px;
    letter-spacing: 0.02em;
    text-transform: uppercase;
    line-height: 1;
  }
  .person-title {
    font-size: 19px;
    font-weight: 500;
    margin-top: 8px;
  }
  .address {
    font-style: normal;
    font-size: 17px;
    font-weight: 500;
    line-height: 1.35;
    margin-top: 22px;
  }
  .contact-list {
    list-style: none;
    margin-top: 20px;
    font-size: 17px;
    font-weight: 500;
  }
  .contact-list li {
    display: flex;
    align-items: center;
    gap: 12px;
    height: 27px;
  }
  .contact-list svg { width: 18px; height: 18px; flex: none; }
  .icon-fill { fill: var(--warm-orange); }
  .icon-stroke { fill: none; stroke: var(--warm-orange); stroke-width: 2; }
  .front-brand {
    position: absolute;
    right: 48px;
    top: 70px;
    display: flex;
    align-items: center;
    gap: 12px;
    color: var(--warm-orange);
    font-weight: 500;
    font-size: 20px;
    letter-spacing: 0.08em;
    text-transform: uppercase;
  }
  .front-brand__square {
    width: 16px;
    height: 16px;
    background: var(--warm-orange);
  }
</style>
</head>
<body>
  <section class="card card--back" aria-label="Card back">
    <h1 class="company-name">RW Holloway LLC</h1>
  </section>

  <section class="card card--front" aria-label="Card front">
    <div class="accent-tab"></div>
    <div class="front-brand"><span class="front-brand__square"></span>RW Holloway LLC</div>
    <div class="contact-block">
      <h2 class="person-name">Dane Whitcombe</h2>
      <p class="person-title">Co-Founder</p>
      <address class="address">4180 N. Cedar Ridge Road<br>Suite 210 Alamo 41</address>
      <ul class="contact-list">
        <li>
          <svg viewBox="0 0 24 24" aria-hidden="true"><path class="icon-fill" d="M6.6 10.8a15 15 0 0 0 6.6 6.6l2.2-2.2a1 1 0 0 1 1-.25 11.4 11.4 0 0 0 3.6.57 1 1 0 0 1 1 1V20a1 1 0 0 1-1 1A17 17 0 0 1 3 4a1 1 0 0 1 1-1h3.5a1 1 0 0 1 1 1c0 1.25.2 2.45.57 3.57a1 1 0 0 1-.25 1z"/></svg>
          555-014-2287
        </li>
        <li>
          <svg viewBox="0 0 24 24" aria-hidden="true"><rect class="icon-fill" x="3" y="5" width="18" height="4" rx="2"/><rect class="icon-fill" x="6" y="10" width="12" height="10" rx="1.5"/></svg>
          555-014-3390
        </li>
        <li>
          <svg viewBox="0 0 24 24" aria-hidden="true"><rect class="icon-fill" x="2" y="5" width="20" height="14" rx="1.5"/><path d="M3 6l9 7 9-7" fill="none" stroke="#fff" stroke-width="1.8"/></svg>
          info@rwhollowayllc
        </li>
        <li>
          <svg viewBox="0 0 24 24" aria-hidden="true"><circle class="icon-stroke" cx="12" cy="12" r="9"/><ellipse class="icon-stroke" cx="12" cy="12" rx="4" ry="9"/><path class="icon-stroke" d="M3 12h18"/></svg>
          www.rwhollowayeng.com
        </li>
      </ul>
    </div>
  </section>
</body>
</html>
```